Government Contracting business needs a website design.

Pellworth & Quine, LLC is a minority owned Service Disabled Veteran Owned Small Business (SDVOSB) that provides Strategic Planning, Public Health Emergency Response, and Data Management Solutions for Federal Civilian and Defense Agencies. We have over 20 years of experience helping health and defense agencies develop concept of operations, deploy assets and personnel in Hot Zones around the world, and deliver goods and services all of the globe.

We are a leader in the field of Data Management. We help our customers develop cloud migration and disaster recovery strategies. We are experts with database management, data replication, queries, consolidation, and records management.

We are looking for a very nice and simple website designs that states clearly what we do as a company and that is easy for our customers to follow. We would like to have some moving pictures that are base on our expertise. We want the website to be easy to use and have the scroll down features that keeps things all on the same page when clicking on the menu. I attached a document with what we need on the website. I will also attach our logo. We want it to look simple clean and very professional.

Target Market(s)

Government Contracting, Management Consulting, Health

Industry/Entity Type

Government

Coding

Coded - Design and coding required

Number of Pages Required

1 page

Font styles to use
Serif

Requirements
Must have
• Very nice picture slides that speaks to our capabilities in Disaster Response, Strategic Planning, and Database Management. Slick look and design. Make sure SDVOSB Logo is right at the beginning of website as our customers is looking for that certification. Very nice colors that blend well with our logo.
Nice to have
• Very nice and slick colors that blends well with logo.
Should not have
• Basic website design that are weary on the eye. No bright colors, just simple colors that looks good with logo.

```html
<!DOCTYPE html>
<html lang="en">
<head>
<meta charset="utf-8">
<title>Pellworth &amp; Quine, LLC</title>
<link rel="stylesheet" href="https://fonts.googleapis.com/css2?family=Crimson+Text:wght@400;600;700&family=Lato:wght@400;700&display=swap">
<style>
:root{
  --slate:#34505f;
  --slate-dark:#2b4553;
  --ink:#2c3a44;
  --muted:#5d6870;
  --rule:#9aa6ad;
  --paper:#ffffff;
  --mist:#ececec;
  --mist-2:#f3f3f3;
}
*{box-sizing:border-box;margin:0;padding:0}
html,body{width:1200px;height:3748px;overflow:hidden}
body{font-family:"Lato",Arial,sans-serif;color:var(--ink);background:var(--paper);position:relative}
section,header,footer{position:absolute;left:0;width:1200px}
.btn{display:inline-block;background:var(--slate);color:#fff;font:700 15px "Lato",Arial,sans-serif;letter-spacing:.5px;padding:12px 20px;text-transform:uppercase}
.btn.light{background:#fff;color:var(--slate)}
.section-title{font-family:"Crimson Text",Georgia,serif;font-size:34px;font-weight:400;text-align:center;color:var(--ink)}
.title-rule{display:block;margin:10px auto 0;width:170px;height:10px}

/* hero */
.hero{top:0;height:680px;background:linear-gradient(100deg,#1c232a 0%,#3a4048 35%,#5b5550 55%,#2d2f33 80%,#1b1f24 100%)}
.hero-photo{position:absolute;inset:0}
.brand{position:absolute;left:40px;top:18px;display:flex;align-items:center;gap:12px;color:#fff}
.brand-mark{width:34px;height:34px;border:2px solid #fff}
.brand-name{font-family:"Crimson Text",Georgia,serif;font-size:26px;line-height:1}
.nav{position:absolute;right:40px;top:40px;display:flex;gap:6px}
.nav a{color:#fff;font:700 13px "Lato",Arial,sans-serif;text-decoration:none;padding:8px 16px;letter-spacing:.5px}
.nav a.active{background:#fff;color:var(--ink)}
.hero-copy{position:absolute;left:40px;top:290px;width:640px;color:#fff}
.hero-copy h1{font-family:"Crimson Text",Georgia,serif;font-size:50px;line-height:1.1;font-weight:700;letter-spacing:1px}
.hero-copy p{font-family:"Crimson Text",Georgia,serif;font-style:italic;font-size:19px;margin:14px 0 22px}
.badge{position:absolute;left:855px;top:300px;width:210px;height:210px}

/* welcome */
.welcome{top:680px;height:568px;background:var(--paper);text-align:center}
.welcome .section-title{margin-top:60px}
.welcome p{width:620px;margin:22px auto 26px;font-size:15px;line-height:1.6;color:var(--muted)}
.partners{position:absolute;top:360px;left:0;width:1200px;display:flex;justify-content:center;gap:80px;align-items:center}
.partner{width:120px;height:120px;border-radius:50%;background:#3b4f76}

/* capabilities */
.capabilities{top:1248px;height:772px;background:var(--mist)}
.capabilities .section-title{margin-top:70px}
.card{position:absolute;width:370px;height:265px;background:#fff;box-shadow:0 2px 8px rgba(0,0,0,.12);padding:100px 30px 0}
.card .icon{position:absolute;left:30px;top:-20px;width:68px;height:68px;background:#fff;box-shadow:0 2px 6px rgba(0,0,0,.18);display:flex;align-items:center;justify-content:center}
.card h3{font-family:"Crimson Text",Georgia,serif;font-size:21px;font-weight:600;color:var(--ink);margin-bottom:8px}
.card ul{list-style:none;font-size:14px;color:var(--muted);line-height:1.6}
.card ul li::before{content:"•";margin-right:8px}
.card .more{display:inline-block;margin-top:8px;font-size:12px;font-weight:700;color:var(--ink);border-bottom:1px solid var(--ink)}

/* why */
.why{top:2020px;height:540px;background:linear-gradient(90deg,#15191d 0%,#2a2e33 45%,#4a4a4c 60%,#26292d 100%)}
.why-copy{position:absolute;left:70px;top:50px;width:520px;color:#fff}
.why-copy h2{font-family:"Crimson Text",Georgia,serif;font-size:34px;font-weight:600;margin-bottom:22px}
.why-copy li{list-style:none;display:flex;gap:12px;font-size:14px;line-height:1.5;margin-bottom:14px}
.why-copy li svg{flex:none;margin-top:3px}
.why-photo{position:absolute;left:640px;top:70px;width:460px;height:410px;background:linear-gradient(160deg,#8fa6c0 0%,#4d6783 50%,#2c3d54 100%)}
.experience{position:absolute;left:700px;top:115px;width:300px;height:300px;background:rgba(40,62,82,.78);color:#fff;display:flex;flex-direction:column;align-items:center;justify-content:center;font-family:"Crimson Text",Georgia,serif}
.experience .num{font-size:80px;line-height:1}
.experience .lbl{font-size:34px}

/* join */
.join{top:2560px;height:408px;background:var(--paper)}
.join-photo{position:absolute;left:70px;top:100px;width:400px;height:230px;background:linear-gradient(135deg,#d9d3c8 0%,#a59783 45%,#5e4f42 100%)}
.join-copy{position:absolute;left:630px;top:80px;width:480px}
.join-copy h2{font-family:"Crimson Text",Georgia,serif;font-size:30px;font-weight:400;text-align:center}
.join-copy p{font-size:13px;line-height:1.6;color:var(--muted);margin:16px 0}
.join-copy h4{font-family:"Crimson Text",Georgia,serif;font-size:22px;font-weight:400;margin-bottom:6px}
.join-copy a{font-size:12px;font-weight:700;color:var(--ink)}

/* contact */
.contact{top:2968px;height:552px;background:var(--mist-2)}
.contact .section-title{margin-top:46px}
.field{position:absolute;background:#fff;border:1px solid #ccd2d6;font-size:14px;color:var(--muted);padding:10px 12px}
.submit{position:absolute;left:110px;top:335px;width:980px;height:50px;background:var(--slate);color:#fff;font:700 16px "Lato",Arial,sans-serif;display:flex;align-items:center;justify-content:center;letter-spacing:1px}

/* footer */
.footer{top:3520px;height:228px;background:var(--slate-dark);color:#fff;text-align:center}
.footer-nav{display:flex;justify-content:center;gap:44px;margin-top:46px;font-size:14px}
.social{display:flex;justify-content:center;gap:18px;margin-top:26px}
.social span{width:40px;height:40px;border:2px solid #fff;border-radius:50%;display:block}
.footer hr{border:0;border-top:1px solid rgba(255,255,255,.3);width:1060px;margin:26px auto 16px}
.copyright{font-size:13px}
</style>
</head>
<body>

<header class="hero">
  <div class="hero-photo" role="img" aria-label="Photograph of business professionals in suits reviewing documents at a meeting table"></div>
  <div class="brand"><span class="brand-mark"></span><span class="brand-name">Pellworth &amp; Quine</span></div>
  <nav class="nav">
    <a class="active">HOME</a><a>ABOUT US</a><a>CORE CAPABILITIES</a><a>WHY HIRE US</a><a>JOIN US</a>
  </nav>
  <div class="hero-copy">
    <h1>LOREM IPSUM IS SIMPLY DUMMY</h1>
    <p>Lorem Ipsum is simply dummy text of the printing and typesetting</p>
    <span class="btn light">Learn More</span>
  </div>
  <svg class="badge" viewBox="0 0 210 210" role="img" aria-label="Service disabled veteran owned small business certification badge">
    <circle cx="105" cy="105" r="100" fill="none" stroke="#fff" stroke-width="4"/>
    <circle cx="105" cy="105" r="78" fill="none" stroke="#fff" stroke-width="2"/>
  </svg>
</header>

<section class="welcome">
  <h2 class="section-title">Welcome to Pellworth &amp; Quine A Health IT Company</h2>
  <svg class="title-rule" viewBox="0 0 170 10"><line x1="0" y1="5" x2="75" y2="5" stroke="#9aa6ad"/><rect x="80" y="1" width="8" height="8" fill="#9aa6ad" transform="rotate(45 84 5)"/><line x1="95" y1="5" x2="170" y2="5" stroke="#9aa6ad"/></svg>
  <p>Pellworth &amp; Quine, LLC is a minority owned Service Disabled Veteran Owned Small Business (SDVOSB) that provides Strategic Planning, Public Health Emergency Response, and Data Management Solutions for Federal Civilian and Defense Agencies. We have over 20 years of experience helping health and defense agencies develop concept of operation.</p>
  <span class="btn">Learn More</span>
  <div class="partners">
    <span class="partner" role="img" aria-label="Partner agency seal"></span>
    <span class="partner" role="img" aria-label="Partner agency seal" style="background:#2f3a2c"></span>
    <span class="partner" role="img" aria-label="Partner agency emblem" style="border-radius:0;width:150px;height:100px;background:#2d5f95"></span>
    <span class="partner" role="img" aria-label="Partner agency emblem" style="border-radius:0;width:150px;height:70px;background:#c8cfd8"></span>
    <span class="partner" role="img" aria-label="Partner agency seal" style="background:#24406a"></span>
  </div>
</section>

<section class="capabilities">
  <h2 class="section-title">Core Capabilities</h2>
  <svg class="title-rule" viewBox="0 0 170 10"><line x1="0" y1="5" x2="75" y2="5" stroke="#9aa6ad"/><rect x="80" y="1" width="8" height="8" fill="#9aa6ad" transform="rotate(45 84 5)"/><line x1="95" y1="5" x2="170" y2="5" stroke="#9aa6ad"/></svg>

  <div class="card" style="left:180px;top:150px">
    <div class="icon"><svg width="38" height="38" viewBox="0 0 38 38" fill="none" stroke="#34505f" stroke-width="2"><circle cx="19" cy="8" r="6"/><line x1="19" y1="14" x2="19" y2="22"/><line x1="6" y1="22" x2="32" y2="22"/><circle cx="6" cy="30" r="5"/><circle cx="19" cy="30" r="5"/><circle cx="32" cy="30" r="5"/></svg></div>
    <h3>Strategic Planning</h3>
    <ul><li>Organizational Needs Assessment</li><li>Roadmap Development</li><li>Marketing Outreach</li></ul>
    <span class="more">READ MORE</span>
  </div>

  <div class="card" style="left:680px;top:150px">
    <div class="icon"><svg width="38" height="38" viewBox="0 0 38 38"><rect x="3" y="9" width="32" height="25" rx="3" fill="#34505f"/><rect x="13" y="4" width="12" height="6" fill="none" stroke="#34505f" stroke-width="2"/><path d="M17 14h4v5h5v4h-5v5h-4v-5h-5v-4h5z" fill="#fff"/></svg></div>
    <h3>Public Health Emergency Response</h3>
    <ul><li>Crisis Management</li><li>Disaster Relief Planning</li><li>Asset and Personnel Deployment</li></ul>
    <span class="more">READ MORE</span>
  </div>

  <div class="card" style="left:180px;top:440px">
    <div class="icon"><svg width="38" height="38" viewBox="0 0 38 38" fill="none" stroke="#34505f" stroke-width="2"><rect x="11" y="11" width="16" height="16"/><path d="M15 11V5M19 11V5M23 11V5M15 33v-6M19 33v-6M23 33v-6M11 15H5M11 19H5M11 23H5M33 15h-6M33 19h-6M33 23h-6"/></svg></div>
    <h3>Data Management Services</h3>
    <ul><li>Cloud Migration Strategy</li><li>Disaster Recovery Strategy</li><li>Records Management</li></ul>
    <span class="more">READ MORE</span>
  </div>

  <div class="card" style="left:680px;top:440px">
    <div class="icon"><svg width="40" height="30" viewBox="0 0 40 30"><rect x="1" y="4" width="24" height="18" fill="#34505f"/><path d="M25 10h8l6 7v5H25z" fill="#34505f"/><circle cx="9" cy="25" r="4" fill="#fff" stroke="#34505f" stroke-width="2"/><circle cx="32" cy="25" r="4" fill="#fff" stroke="#34505f" stroke-width="2"/></svg></div>
    <h3>Contracts Vehicles</h3>
    <ul><li>SDVOSB Sole Source</li><li>Federal IT Supply Schedule (Sub)</li><li>Multi-Agency Services Pool (Sub)</li></ul>
    <span class="more">READ MORE</span>
  </div>
</section>

<section class="why">
  <div class="why-copy">
    <h2>Why Hire Us?</h2>
    <ul>
      <li><svg width="14" height="14" viewBox="0 0 14 14"><path d="M7 0l2 5h5l-4 3 1.6 5L7 10l-4.6 3L4 8 0 5h5z" fill="#fff"/></svg><span>Over 20 years of experience deploying assets and personnel to disaster zones around the US and the world.</span></li>
      <li><svg width="14" height="14" viewBox="0 0 14 14"><path d="M7 0l2 5h5l-4 3 1.6 5L7 10l-4.6 3L4 8 0 5h5z" fill="#fff"/></svg><span>Over 20 years of experience developing concept of operations and stakeholder management strategies for Federal Agencies.</span></li>
      <li><svg width="14" height="14" viewBox="0 0 14 14"><path d="M7 0l2 5h5l-4 3 1.6 5L7 10l-4.6 3L4 8 0 5h5z" fill="#fff"/></svg><span>Over 15 years of experience with database management and replication.</span></li>
      <li><svg width="14" height="14" viewBox="0 0 14 14"><path d="M7 0l2 5h5l-4 3 1.6 5L7 10l-4.6 3L4 8 0 5h5z" fill="#fff"/></svg><span>Highly educated consultants with over 90% possessing advance degrees and industry certifications.</span></li>
    </ul>
    <span class="btn light" style="margin-top:18px">Learn More</span>
  </div>
  <div class="why-photo" role="img" aria-label="Photograph of a government capitol building under a blue sky"></div>
  <div class="experience"><span class="num">20</span><span class="lbl">Years Experience</span></div>
</section>

<section class="join">
  <div class="join-photo" role="img" aria-label="Photograph of hands signing documents at a desk"></div>
  <div class="join-copy">
    <h2>Join Us</h2>
    <svg class="title-rule" viewBox="0 0 170 10"><line x1="0" y1="5" x2="75" y2="5" stroke="#9aa6ad"/><rect x="80" y="1" width="8" height="8" fill="#9aa6ad" transform="rotate(45 84 5)"/><line x1="95" y1="5" x2="170" y2="5" stroke="#9aa6ad"/></svg>
    <p>Pellworth &amp; Quine strives to provide an outstanding work environment for our employees. We invest in our people and believe strongly in creating an environment where our employees are free to work on innovative solutions that meet our clients' needs. <a>READ MORE</a></p>
    <h4>Job Openings</h4>
    <p style="margin-top:0">We are always recruiting for key positions. If you want to bring your talent to us, submit your resume against the key positions.</p>
    <span class="btn">Upload Resume</span>
  </div>
</section>

<section class="contact">
  <h2 class="section-title">Get In Touch</h2>
  <svg class="title-rule" viewBox="0 0 170 10"><line x1="0" y1="5" x2="75" y2="5" stroke="#9aa6ad"/><rect x="80" y="1" width="8" height="8" fill="#9aa6ad" transform="rotate(45 84 5)"/><line x1="95" y1="5" x2="170" y2="5" stroke="#9aa6ad"/></svg>
  <div class="field" style="left:110px;top:140px;width:310px;height:42px">Name</div>
  <div class="field" style="left:445px;top:140px;width:310px;height:42px">E-mail</div>
  <div class="field" style="left:780px;top:140px;width:310px;height:42px">Phone</div>
  <div class="field" style="left:110px;top:205px;width:980px;height:110px">Message</div>
  <div class="submit">SUBMIT</div>
</section>

<footer class="footer">
  <div class="footer-nav"><span>Home</span><span>About Us</span><span>Core Capabilities</span><span>Why Hire Us?</span><span>Join Us</span></div>
  <div class="social"><span></span><span></span><span></span></div>
  <hr>
  <div class="copyright">© PELLWORTH &amp; QUINE - 2018, All Rights Reserved</div>
</footer>

</body>
</html>
```